Home Security Company Business Card

Looking for a eye catching business card that is non traditional and stands out but yet still looks professional. It should include all the pertinent information such as name, title, address, telephone, e-mail, website address should definitely stand out and then finally the logo.

Target Market(s)

Residential and Commercial accounts mostly upscale accounts

Industry/Entity Type

Security

Contact Information for Business Card

Name
Title
Address
Office #
Cell #
E-mail
Website

Font styles to use
Serif
Sans Serif

Requirements
Must have
• Logo, two sided color configuration
Nice to have
• You decide
Should not have
• There really aren't any.

```html
<!DOCTYPE html>
<html lang="en">
<head>
<meta charset="utf-8">
<title>Veyra Protection Group — Business Card</title>
<link rel="stylesheet" href="https://fonts.googleapis.com/css2?family=Lato:wght@400;700&display=swap">
<style>
  :root {
    --backdrop: #2b2b2b;
    --card: #ffffff;
    --card-shade: #f1f1f1;
    --crimson: #8a1512;
    --gold: #d9a531;
    --gold-dark: #b9851d;
    --ink: #1a1a1a;
    --muted: #333333;
  }
  * { box-sizing: border-box; margin: 0; padding: 0; }
  html, body { width: 1200px; height: 997px; overflow: hidden; }
  body {
    background: var(--backdrop);
    font-family: "Lato", Arial, sans-serif;
    position: relative;
  }
  .card {
    position: absolute;
    left: 320px;
    width: 560px;
    height: 320px;
    background: linear-gradient(160deg, var(--card), var(--card-shade));
    box-shadow: 0 14px 40px rgba(0,0,0,.55);
    overflow: hidden;
  }
  .card--front { top: 110px; }
  .card--back { top: 540px; }

  .brand {
    display: flex;
    align-items: center;
    gap: 16px;
    color: var(--crimson);
    font-family: "Lato", Arial, sans-serif;
    font-weight: 700;
  }
  .brand__mark {
    flex: none;
    width: 48px;
    height: 48px;
    border-radius: 50%;
    background: var(--crimson);
  }
  .card--front .brand {
    position: absolute;
    left: 60px; top: 0; bottom: 0;
    font-size: 30px;
    line-height: 1.2;
  }
  .card--back .brand {
    position: absolute;
    left: 28px; top: 118px;
    width: 210px;
    font-size: 20px;
    line-height: 1.25;
    gap: 12px;
  }
  .card--back .brand__mark { width: 32px; height: 32px; }

  .divider {
    position: absolute;
    left: 254px; top: 46px;
    width: 3px; height: 190px;
    background: var(--ink);
  }
  .contact {
    position: absolute;
    left: 280px; top: 50px;
    right: 16px;
  }
  .contact__name {
    font-size: 22px;
    color: var(--crimson);
    font-weight: 400;
  }
  .contact__name strong { font-weight: 700; }
  .contact__title {
    font-size: 12px;
    color: var(--muted);
    margin-top: 2px;
  }
  .contact__list {
    list-style: none;
    margin-top: 34px;
    font-size: 13px;
    color: var(--ink);
  }
  .contact__list li {
    display: flex;
    align-items: center;
    gap: 12px;
    height: 22px;
    white-space: nowrap;
  }
  .contact__list svg { width: 14px; height: 14px; fill: var(--crimson); flex: none; }

  .band--gold {
    position: absolute;
    left: 0; bottom: 0;
    width: 100%; height: 14px;
    background: linear-gradient(90deg, var(--gold-dark), var(--gold));
  }
  .band--crimson {
    position: absolute;
    right: 0; bottom: 14px;
    width: 220px; height: 24px;
    background: var(--crimson);
    border-top-left-radius: 24px;
  }
</style>
</head>
<body>
  <section class="card card--front" aria-label="Card front">
    <div class="brand">
      <span class="brand__mark"></span>
      <span class="brand__name">Veyra<br>Protection Group</span>
    </div>
  </section>

  <section class="card card--back" aria-label="Card back">
    <div class="brand">
      <span class="brand__mark"></span>
      <span class="brand__name">Veyra<br>Protection Group</span>
    </div>

    <div class="divider"></div>

    <div class="contact">
      <h1 class="contact__name"><strong>Laurent</strong> Mercier</h1>
      <p class="contact__title">Director / Owner</p>
      <ul class="contact__list">
        <li>
          <svg viewBox="0 0 16 16" aria-hidden="true"><path d="M3 1h3l1.5 4-2 1.3a9 9 0 0 0 4.2 4.2l1.3-2 4 1.5v3a2 2 0 0 1-2 2A13 13 0 0 1 1 3a2 2 0 0 1 2-2z"/></svg>
          +33612345678
        </li>
        <li>
          <svg viewBox="0 0 16 16" aria-hidden="true"><path d="M1 3h14v10H1z M1 3l7 6 7-6" fill="none" stroke="#8a1512" stroke-width="1.6"/></svg>
          laurent.m@veyraprotection.com
        </li>
        <li>
          <svg viewBox="0 0 16 16" aria-hidden="true"><path d="M6.5 9.5l3-3M7 4l1.5-1.5a3 3 0 0 1 4.2 4.2L11 8.5M9 12l-1.5 1.5a3 3 0 0 1-4.2-4.2L5 7.5" fill="none" stroke="#8a1512" stroke-width="1.8" stroke-linecap="round"/></svg>
          www.veyraprotection.com
        </li>
        <li>
          <svg viewBox="0 0 16 16" aria-hidden="true"><path d="M8 1l7 6.5h-2V15H9.5v-4h-3v4H3V7.5H1z"/></svg>
          14 rue des Lilas, 75011 Paris
        </li>
      </ul>
    </div>

    <div class="band--crimson"></div>
    <div class="band--gold"></div>
  </section>
</body>
</html>
```